Brightfield Ventures Inc. Letterhead

Creation of attractive and eye catching letterhead for a business start-up for the construction industry. Letterhead must relate to construction, but avoid standard hammer and tools in the design.

I forgot to add some details, sorry about that. Some pertinent info: Ph: 916-555-0187 brightfieldventures.example 448 Willowmere Ave, Ste 210 Folsom, CA 95999 info@brightfieldventures.example not sure if slogan should be in there" “Connecting construction professionals to create a purpose driven industry.” must be able to be used in word. Thanks!

```html
<!DOCTYPE html>
<html lang="en">
<head>
<meta charset="utf-8">
<title>Brightfield Ventures Inc. Letterhead</title>
<link href="https://fonts.googleapis.com/css2?family=Lato:wght@400;700&family=Montserrat:wght@600&family=Yellowtail&display=swap" rel="stylesheet">
<style>
  :root {
    --navy: #1b1f5c;
    --red: #c4202a;
    --ink: #545454;
    --muted: #5f5f5f;
    --paper: #ffffff;
  }
  * { margin: 0; padding: 0; box-sizing: border-box; }
  html, body { width: 909px; height: 1200px; overflow: hidden; background: var(--paper); }
  .letterhead {
    position: relative;
    width: 909px;
    height: 1200px;
    background: var(--paper);
    font-family: "Lato", sans-serif;
    color: var(--ink);
  }
  .header-band, .footer-band { position: absolute; left: 0; width: 909px; }
  .header-band { top: 0; height: 80px; }
  .footer-band { bottom: 0; height: 110px; }

  .company-name {
    position: absolute;
    top: 114px;
    left: 0;
    width: 909px;
    display: flex;
    justify-content: center;
    align-items: center;
    gap: 10px;
    font-family: "Montserrat", sans-serif;
    font-weight: 600;
    font-size: 19px;
    letter-spacing: 1.5px;
    color: var(--navy);
  }
  .company-name .mark { width: 14px; height: 14px; background: var(--red); }

  .address, .contact {
    position: absolute;
    top: 120px;
    font-size: 12.5px;
    line-height: 20px;
    color: var(--muted);
    white-space: nowrap;
  }
  .address {
    right: 660px;
    text-align: right;
    padding-right: 14px;
    border-right: 2px solid var(--red);
  }
  .contact {
    left: 634px;
    padding-left: 12px;
    border-left: 2px solid var(--red);
  }
  .contact .line { display: flex; align-items: center; gap: 5px; }
  .contact svg { width: 10px; height: 10px; fill: var(--red); }

  .letter { position: absolute; top: 230px; left: 75px; width: 755px; }
  .greeting { font-weight: 700; font-size: 16px; color: var(--navy); margin-bottom: 18px; }
  .letter p.body-text {
    font-size: 16.5px;
    line-height: 27.3px;
    text-align: justify;
    hyphens: auto;
    -webkit-hyphens: auto;
    margin-bottom: 20px;
    color: var(--ink);
  }
  .closing { margin-top: 24px; font-size: 19px; color: #2a2a2a; }
  .signature {
    font-family: "Yellowtail", "Brush Script MT", cursive;
    font-size: 36px;
    color: var(--navy);
    line-height: 1.2;
  }
  .website {
    position: absolute;
    left: 75px;
    top: 1138px;
    font-size: 14.5px;
    letter-spacing: 1px;
    color: var(--muted);
  }
  .website .name { font-weight: 700; color: var(--navy); }
</style>
</head>
<body>
<main class="letterhead">
  <svg class="header-band" viewBox="0 0 909 80" aria-hidden="true">
    <polygon points="0,0 909,0 909,58 454,5 0,58" fill="var(--navy)"/>
    <polyline points="0,65 454,12 909,65" fill="none" stroke="var(--red)" stroke-width="3"/>
  </svg>

  <div class="address">448 Willowmere Ave, Ste 210<br>Folsom, CA 95999</div>

  <div class="company-name"><span class="mark"></span>BRIGHTFIELD VENTURES</div>

  <div class="contact">
    <div class="line">
      <svg viewBox="0 0 10 10"><path d="M2 0 L4 2.5 L3 3.8 Q4.5 6 6.2 7 L7.5 6 L10 8 L8.5 10 Q3 9 0 1.5 Z"/></svg>
      916-555-0187
    </div>
    <div class="line">
      <svg viewBox="0 0 10 10"><path d="M0 2 H10 V9 H0 Z M0.8 2.6 L5 6 L9.2 2.6" stroke="#fff" stroke-width="0.8"/></svg>
      info@brightfieldventures.example
    </div>
  </div>

  <section class="letter">
    <p class="greeting">Dear Mr. Lorem,</p>
    <p class="body-text">Lorem ipsum dolor sit amet, consectetuer adipiscing elit, sed diam nonummy nibh euismod tincidunt ut laoreet dolore magna aliquam erat volutpat. Ut wisi enim ad minim veniam, quis nostrud exerci tation ullamcorper suscipit lobortis nisl ut aliquip ex ea commodo consequat. Duis autem vel eum iriure dolor in hendiusto odio dignissim qui blandit praesent luptatum zzril delenit augue duis dolore te feugait nulla facilisi.</p>
    <p class="body-text">Lorem ipsum dolor sit amet, consectetuer adipiscing elit, sed diam nonummy nibh euismod tincidunt ut laoreet dolore magna aliquam erat volutpat. Ut wisi enim ad minim veniam, quis nostrud exerci tation ullamcorper suscipit lobortis nisl ut aliquip ex ea commodo consequat. Duis autem vel eum iriure dolor in hendiusto odio dignissim qui blandit praesent luptatum zzril delenit augue duis dolore te feugait nulla facilisi.</p>
    <p class="body-text">Lorem ipsum dolor sit amet, consectetuer adipiscing elit, sed diam nonummy nibh euismod tincidunt ut laoreet dolore magna aliquam erat volutpat. Ut wisi enim ad minim veniam, quis nostrud exerci tation ullamcorper suscipit lobortis nisl ut aliquip ex ea commodo consequat. Duis autem vel eum iriure dolor in hendiusto odio dignissim qui blandit praesent luptatum zzril delenit augue duis dolore te feugait nulla facilisi.</p>
    <p class="closing">Sincerely Your,</p>
    <p class="signature">Your Name</p>
  </section>

  <p class="website">www.<span class="name">brightfieldventures</span>.example</p>

  <svg class="footer-band" viewBox="0 1090 909 110" aria-hidden="true">
    <path d="M0 1098 H22 V1150 Q22 1170 42 1170 H700 Q720 1170 720 1150 V1120 Q720 1098 742 1098 H909 V1110 H750 Q734 1110 734 1126 V1160 Q734 1200 694 1200 H0 Z" fill="var(--navy)"/>
    <rect x="760" y="1138" width="149" height="62" fill="var(--red)"/>
  </svg>
</main>
</body>
</html>
```